Business card design needed

The company name is Pellow Architects. We are an architectural company based in Melbourne,Australia that has a mix of client base from health care, commercial office, aged care, multi-residential, single residential and retail. Design type is contemporary.

Suggest the base colours need to be black and white. Please leave an area on the back of the card available for handwritten notes.

Target Market(s)

Generally corporate, aged 30 to 65

Industry/Entity Type

Residential

Contact Information for Business Card

Pellow Architects
Dale Pellow
14 Mosley Street
Fenwick Vale VIC 3074
T (03) 9572 4016
M 0437 619 258
E dp@pellowarc.com.au

Logo Text

PA

Logo styles of interest
Emblem Logo
Abstract Logo
Lettermark Logo
Requirements
Must have
• I am having trouble attaching a sketch so would really appreciate your effort to try the following brief.

Black and White (B&W)
Would like different card cutout profile. Logo Example, use the half circle curve of the G to form the left edge of the card with no margin. The A is to sit inside the G, connected to the G by its horizontal. The A has its cross bar and lower right leg removed. Card in black, text in white.

Back of card to be black text on white background with services provided.

Client Focused Service
Architecture and Design
Functional Planning
Town Planning
Feasability Studies
Contract Documentation
Contract Administration
Project Management

Simple elegant text, Ariel or similar
Nice to have
• Integrated logo and card cut-out.

Card base black on front, white on back
Should not have
• Too many colours
Fussy details

```html
<!DOCTYPE html>
<html lang="en">
<head>
<meta charset="utf-8">
<title>Pellow Architects – Business Card</title>
<link href="https://fonts.googleapis.com/css2?family=Jost:wght@300&display=swap" rel="stylesheet">
<style>
  :root {
    --card-black: #0b0b0b;
    --sky-white: #ffffff;
    --ink-white: #ffffff;
    --skyline-grey: #1a1a1a;
  }
  html, body {
    margin: 0;
    padding: 0;
    width: 1200px;
    height: 664px;
    overflow: hidden;
    background: var(--sky-white);
  }
  .card {
    position: relative;
    width: 1200px;
    height: 664px;
    overflow: hidden;
    background: var(--card-black);
    font-family: "Jost", "Helvetica Neue", Arial, sans-serif;
    font-weight: 300;
    color: var(--ink-white);
  }
  .skyline-artwork {
    position: absolute;
    inset: 0;
    background: linear-gradient(
      to bottom,
      var(--sky-white) 0%,
      var(--sky-white) 12%,
      var(--skyline-grey) 34%,
      var(--card-black) 60%,
      var(--card-black) 100%
    );
  }
  .brand-mark {
    position: absolute;
    left: 0;
    top: 292px;
    width: 190px;
    height: 190px;
  }
  .brand-name {
    position: absolute;
    left: 200px;
    top: 310px;
    margin: 0;
    font-size: 60px;
    font-weight: 300;
    line-height: 92px;
    letter-spacing: 0.16em;
    text-transform: uppercase;
  }
  .brand-name span { display: block; }
  .contact {
    position: absolute;
    left: 30px;
    top: 524px;
    margin: 0;
    font-size: 23px;
    line-height: 41px;
    letter-spacing: 0.01em;
  }
  .contact p { margin: 0; }
</style>
</head>
<body>
  <main class="card">
    <div class="skyline-artwork" role="img" aria-label="City skyline silhouette in black over a faint architectural plan, rising against a white sky"></div>

    <svg class="brand-mark" viewBox="0 0 190 190" aria-hidden="true">
      <circle cx="92" cy="93" r="84" fill="none" stroke="var(--ink-white)" stroke-width="10"/>
    </svg>

    <h1 class="brand-name">
      <span>Pellow</span>
      <span>Architects</span>
    </h1>

    <address class="contact">
      <p>Dale Pellow 14 Mosley Street Fenwick Vale VIC 3074</p>
      <p>Tel (03) 9572 4016 M 0437 619 258</p>
      <p>Email: dp@pellowarc.com.au</p>
    </address>
  </main>
</body>
</html>
```